Need Flyer for Our Real estate Agency

Need to run General Campaign for our agency with Start of New Year as our theme ..Must have an agent's picture on the DL..
Address:
27 / 486Brindle rd, Marsden VIC 3047
Ph:03 9412 7306
email:info@kovalinrealestate.com.au
www.kovalinrealestate.com.au
Something like as attached picture..
Target Market(s)
Home Buyers
Industry/Entity Type
Real Estate Agent
Requirements
Must have
- Our Logo Colours

```html
<!DOCTYPE html>
<html lang="en">
<head>
<meta charset="utf-8">
<title>Kovalin Real Estate – New Year DL Flyer</title>
<link rel="stylesheet" href="https://fonts.googleapis.com/css2?family=Lato:wght@300;400&family=Open+Sans:wght@400;700&display=swap">
<style>
  :root {
    --navy: #0f2559;
    --navy-deep: #0a1b45;
    --navy-light: #1b3a7e;
    --red: #7a121d;
    --grey: #c9cbd0;
    --white: #ffffff;
    --page: #ebebeb;
  }
  * { box-sizing: border-box; margin: 0; padding: 0; }
  html, body { width: 1200px; height: 1198px; overflow: hidden; }
  body { background: var(--page); position: relative; font-family: "Lato", sans-serif; color: var(--white); }

  .card {
    position: absolute; left: 106px; width: 988px; height: 469px; overflow: hidden;
    box-shadow: 0 4px 10px rgba(0,0,0,.25);
  }
  .card--front { top: 72px; }
  .card--back { top: 614px; }
  .card__art { position: absolute; inset: 0; width: 988px; height: 469px; }

  .brand { position: absolute; text-align: center; font-family: "Lato", sans-serif; font-weight: 400; color: var(--white); }
  .brand__name { display: block; font-size: 50px; letter-spacing: 5px; line-height: 1; }
  .brand__tag { display: block; font-size: 11px; letter-spacing: 3px; margin-top: 8px; border-top: 1px solid var(--white); padding-top: 5px; }

  .card--front .brand { left: 133px; top: 118px; width: 280px; }
  .headline { position: absolute; left: 40px; top: 220px; width: 470px; text-align: center; font-weight: 300; font-size: 33px; line-height: 46px; }
  .subline { position: absolute; left: 20px; top: 330px; width: 510px; text-align: center; font-family: "Open Sans", sans-serif; font-size: 15.5px; }
  .subline strong { font-weight: 700; }
  .cta {
    position: absolute; left: 85px; top: 380px; width: 372px; height: 46px; border-radius: 23px;
    background: var(--white); color: var(--red); font-family: "Open Sans", sans-serif; font-weight: 700; font-size: 21px;
    display: flex; align-items: center; justify-content: center; gap: 8px; box-shadow: 0 3px 6px rgba(0,0,0,.35);
  }
  .cta svg { width: 20px; height: 20px; }
  .appraisal { position: absolute; left: 85px; top: 435px; width: 372px; text-align: center; font-weight: 300; font-size: 18px; }

  .card--back .brand { left: 577px; top: 122px; width: 280px; }
  .contact { position: absolute; left: 566px; top: 225px; font-weight: 300; }
  .contact__role { font-size: 22px; margin-bottom: 14px; }
  .contact__row { display: flex; align-items: center; gap: 12px; font-size: 19px; height: 37px; }
  .contact__row svg { width: 18px; height: 18px; flex: none; }
  .address { position: absolute; right: 52px; top: 424px; font-weight: 300; font-size: 20px; }
</style>
</head>
<body>

<section class="card card--front">
  <svg class="card__art" viewBox="0 0 988 469" aria-hidden="false">
    <defs>
      <linearGradient id="navyFront" x1="0" y1="0" x2="1" y2="0">
        <stop offset="0" stop-color="var(--navy-deep)"/>
        <stop offset=".7" stop-color="var(--navy)"/>
        <stop offset="1" stop-color="var(--navy-light)"/>
      </linearGradient>
      <linearGradient id="agentPhoto" x1="0" y1="0" x2="0" y2="1">
        <stop offset="0" stop-color="#9fb8d8"/>
        <stop offset=".45" stop-color="#8d8a86"/>
        <stop offset=".8" stop-color="#4d566e"/>
        <stop offset="1" stop-color="#4e6b3a"/>
      </linearGradient>
    </defs>
    <rect width="988" height="469" fill="url(#navyFront)"/>
    <rect y="395" width="988" height="4" fill="var(--white)"/>
    <rect y="399" width="988" height="70" fill="var(--red)"/>
    <path d="M592 0 C520 120 520 340 578 469 H988 V0 Z" fill="var(--grey)"/>
    <path d="M620 0 C548 120 548 340 596 469 H988 V0 Z" fill="var(--white)"/>
    <path d="M640 0 C568 120 566 340 610 469 H988 V0 Z" fill="url(#agentPhoto)" role="img" aria-label="Photo of the agent in a grey suit standing in front of a lit two-storey family home"/>
  </svg>

  <div class="brand">
    <span class="brand__name">KOVALIN</span>
    <span class="brand__tag">REAL ESTATE</span>
  </div>
  <p class="headline">Curios to know what your<br>home is worth?</p>
  <p class="subline">START OF NEW YEAR WITH <strong>ARJUN MEHTA</strong> AND FIND OUT!</p>
  <div class="cta">
    <span>CALL ME NOW!</span>
    <svg viewBox="0 0 20 20" aria-hidden="true"><circle cx="10" cy="10" r="8.5" fill="none" stroke="currentColor" stroke-width="1.8"/><path d="M7 5.5l1.6 2.4-1 1.1c.6 1.3 1.5 2.2 2.6 2.8l1.1-1 2.4 1.5-.7 1.7c-3.6-.2-6.8-3.4-7-7z" fill="currentColor"/></svg>
    <span>03 9412 7306</span>
  </div>
  <p class="appraisal">For Free property Appraisal</p>
</section>

<section class="card card--back">
  <svg class="card__art" viewBox="0 0 988 469">
    <defs>
      <linearGradient id="navyBack" x1="0" y1="0" x2="1" y2="0">
        <stop offset="0" stop-color="var(--navy-light)"/>
        <stop offset=".5" stop-color="var(--navy)"/>
        <stop offset="1" stop-color="var(--navy-deep)"/>
      </linearGradient>
      <linearGradient id="handsPhoto" x1="0" y1="0" x2="1" y2="1">
        <stop offset="0" stop-color="#c9cdd2"/>
        <stop offset=".35" stop-color="#d9b7a2"/>
        <stop offset=".6" stop-color="#d8574f"/>
        <stop offset="1" stop-color="#2a3a4c"/>
      </linearGradient>
    </defs>
    <rect width="988" height="469" fill="url(#navyBack)"/>
    <rect y="400" width="988" height="4" fill="var(--white)"/>
    <rect y="404" width="988" height="65" fill="var(--red)"/>
    <path d="M0 0 H345 C440 110 440 330 395 469 H0 Z" fill="var(--grey)"/>
    <path d="M0 0 H315 C415 110 418 330 375 469 H0 Z" fill="var(--white)"/>
    <path d="M0 0 H290 C390 110 395 330 355 469 H0 Z" fill="url(#handsPhoto)" role="img" aria-label="Photo of two hands sheltering a small red model house"/>
  </svg>

  <div class="brand">
    <span class="brand__name">KOVALIN</span>
    <span class="brand__tag">REAL ESTATE</span>
  </div>
  <div class="contact">
    <p class="contact__role">Arjun Mehta, Sales Manager</p>
    <p class="contact__row">
      <svg viewBox="0 0 20 20" aria-hidden="true"><circle cx="10" cy="10" r="8.5" fill="none" stroke="#fff" stroke-width="1.6"/><path d="M7 5.5l1.6 2.4-1 1.1c.6 1.3 1.5 2.2 2.6 2.8l1.1-1 2.4 1.5-.7 1.7c-3.6-.2-6.8-3.4-7-7z" fill="#fff"/></svg>
      0421 587 314
    </p>
    <p class="contact__row">
      <svg viewBox="0 0 20 20" aria-hidden="true"><circle cx="10" cy="10" r="8.5" fill="none" stroke="#fff" stroke-width="1.6"/><rect x="5.5" y="7" width="9" height="6.5" fill="#fff"/><path d="M5.5 7l4.5 3.5L14.5 7" fill="none" stroke="var(--navy)" stroke-width="1"/></svg>
      arjun.mehta@kovalinrealestate.com.au
    </p>
    <p class="contact__row">
      <svg viewBox="0 0 20 20" aria-hidden="true" fill="none" stroke="#fff" stroke-width="1.4"><circle cx="10" cy="10" r="8.5"/><ellipse cx="10" cy="10" rx="3.5" ry="8.5"/><path d="M1.5 10h17M3 6h14M3 14h14"/></svg>
      www.kovalinrealestate.com.au
    </p>
  </div>
  <p class="address">27/486 Brindle Rd Marsden, Victoria, Australia 3047</p>
</section>

</body>
</html>
```